Zelvo Stationary

Design the stationary of Zelvo Promotions Group.

Zelvo is a BTL company, BTL meaning "below the line". In other words Zelvo is a Promotional Marketing company (the company that design the brands promotional activities).

The design should transmit creativity, agility, boldness.

I need:
* Bis Card
* Letter head
* Envelopes, both vertical and horizontal (for legal size), and letter envelope
* Folders
* PPT template (Title page and regular page)
* CD slip (CD envelope)
* ID card (employee card)

And what ever else you want to throw in.
Updates

Guys,

Something I missed from the brief.   The predominat color should be RED.

Also, have fun and play with the exclamation mark (!) of the logo. 

Hi guys, more comments:

Remember that Zelvo is a "creativity" agency, not in the advertising side but on the promotional side, and that should reflect on the stationary.

 I want a bold design.  Bold and yet crisp.

 

Guys, i just uploaded the Logo in AI format.

I Also uploaded the actual Zelvo Bis Card, wich I like.  So I will like to see some designs with that bis card approach.

Guys, I am so sorry, but I notice in your last post that I upladed a wrong design ("13154_promotions_group_zelvo_brief225630.ai").  The problem was that I asked the designer the file in AI format and he send me thw wrong file, and since I dont have Illustrator I could not verify it.

The differences are minor, I just already ask him the correct one (similar to the EPS file).

Sorry                                   

Just post the correct AI file : "Zelvo Logo.ai"

Reason: I'm expecting more designs to choose from and also I wont be available tomorrow to decide.

Reason: Sorry guys, but we are not there yet!

Target Market(s)

Marketing directors, Marketing Managers

Industry/Entity Type

Legal

Requirements
Must have
• Must work with the logo attached.
The predominat color should be RED.
Play and have fun with the exclamation mark (!).
Should not have
• * No old fonts

Should not be:
* boring
* Informal
* rigid

```html
<!DOCTYPE html>
<html lang="en">
<head>
<meta charset="utf-8">
<title>Zelvo Promotions Group – Stationery</title>
<link href="https://fonts.googleapis.com/css2?family=Archivo:wght@400;700;800&display=swap" rel="stylesheet">
<style>
  :root {
    --red: #b3121b;
    --red-deep: #8f0d14;
    --ink: #1a1a1a;
    --grey: #6b6b6b;
    --paper: #ffffff;
    --board: #ffffff;
  }
  * { box-sizing: border-box; margin: 0; padding: 0; }
  html, body { width: 1200px; height: 900px; overflow: hidden; background: var(--board); }
  body { font-family: "Archivo", Arial, sans-serif; color: var(--ink); position: relative; }

  .section-label { position: absolute; font-weight: 700; font-size: 26px; color: var(--ink); }
  .section-label--envelopes { left: 56px; top: 78px; }
  .section-label--id { left: 740px; top: 30px; }

  .wordmark { font-weight: 800; color: var(--ink); letter-spacing: -0.5px; display: flex; align-items: center; gap: 8px; line-height: 1; }
  .wordmark__dot { width: 14px; height: 14px; border-radius: 50%; background: var(--red); }
  .wordmark__sub { font-weight: 800; font-size: 11px; color: var(--ink); letter-spacing: 1.6px; margin-top: 4px; }

  /* Large envelope */
  .envelope-large {
    position: absolute; left: 60px; top: 136px; width: 1050px; height: 714px;
    background: var(--paper); border: 1px solid #d6d6d6;
    box-shadow: 4px 6px 8px rgba(0,0,0,0.35);
  }
  .envelope-large .brand { position: absolute; left: 70px; top: 42px; }
  .envelope-large .wordmark { font-size: 46px; }
  .contact { position: absolute; left: 80px; top: 162px; font-size: 12.5px; line-height: 17px; color: var(--ink); }
  .contact__lines { margin-top: 24px; }
  .contact__key { color: var(--red); font-weight: 700; }
  .contact__web { margin-top: 16px; font-weight: 700; }
  .exclaim-area {
    position: absolute; left: 70px; top: 320px; width: 190px; height: 392px;
    background: linear-gradient(160deg, var(--red) 0%, var(--red-deep) 55%, var(--ink) 100%);
    border-radius: 4px 4px 95px 95px;
  }

  /* Small envelope */
  .envelope-small {
    position: absolute; left: 410px; top: 520px; width: 680px; height: 290px;
    background: var(--paper); border: 1px solid #d6d6d6;
    box-shadow: 3px 5px 7px rgba(0,0,0,0.35);
    transform: rotate(-9deg); transform-origin: center;
    overflow: hidden;
  }
  .envelope-small .brand { position: absolute; left: 48px; top: 26px; }
  .envelope-small .wordmark { font-size: 22px; gap: 5px; }
  .envelope-small .wordmark__dot { width: 8px; height: 8px; }
  .envelope-small .wordmark__sub { font-size: 5.5px; letter-spacing: 0.9px; margin-top: 2px; }
  .envelope-small .contact { left: 52px; top: 78px; font-size: 6.5px; line-height: 9px; }
  .envelope-small .contact__lines { margin-top: 8px; }
  .envelope-small .contact__web { margin-top: 8px; }
  .envelope-small .exclaim-area { left: 50px; top: 150px; width: 84px; height: 150px; border-radius: 3px 3px 42px 42px; }

  /* ID card */
  .id-card {
    position: absolute; left: 690px; top: 76px; width: 506px; height: 320px;
    background: var(--paper); border-radius: 28px; overflow: hidden;
    border: 1px solid #d0d0d0; box-shadow: 3px 5px 7px rgba(0,0,0,0.35);
  }
  .id-card__band { position: absolute; top: 0; right: 0; width: 240px; height: 100%; }
  .id-card .brand { position: absolute; left: 24px; top: 56px; }
  .id-card .wordmark { font-size: 44px; }
  .id-card__holder { position: absolute; left: 24px; top: 180px; font-size: 12.5px; line-height: 17px; }
  .id-card__name { font-size: 19px; font-weight: 400; letter-spacing: 0.3px; line-height: 24px; display: flex; align-items: center; gap: 6px; }
  .id-card__name strong { font-weight: 800; }
  .id-card__flag { width: 14px; height: 8px; background: var(--red); clip-path: polygon(0 0,100% 0,0 100%); }
  .id-card__web { position: absolute; left: 24px; top: 272px; font-weight: 700; font-size: 12.5px; }
  .id-card__badge { position: absolute; right: 22px; top: 180px; text-align: center; color: var(--paper); line-height: 0.9; }
  .id-card__badge-id { font-size: 92px; font-weight: 800; color: var(--ink); letter-spacing: -2px; }
  .id-card__badge-card { font-size: 36px; font-weight: 800; }
</style>
</head>
<body>

  <h2 class="section-label section-label--envelopes">Envelopes</h2>
  <h2 class="section-label section-label--id">ID card</h2>

  <section class="envelope-large" aria-label="Letter envelope">
    <div class="brand">
      <div class="wordmark">zelvo<span class="wordmark__dot"></span></div>
      <div class="wordmark__sub">PROMOTIONS GROUP</div>
    </div>
    <address class="contact" style="font-style:normal">
      27 Calle Ámbar, Los Prados,<br>Santo Domingo<br>Dominican Republic
      <div class="contact__lines">
        <span class="contact__key">P:</span> +809 555 0101<br>
        <span class="contact__key">F:</span> +809 555 0102<br>
        <span class="contact__key">E:</span> info@zelvo.com.do
      </div>
      <div class="contact__web">www.zelvo.com.do</div>
    </address>
    <div class="exclaim-area" role="img" aria-label="Large brand exclamation mark decoration"></div>
  </section>

  <section class="envelope-small" aria-label="Legal envelope">
    <div class="brand">
      <div class="wordmark">zelvo<span class="wordmark__dot"></span></div>
      <div class="wordmark__sub">PROMOTIONS GROUP</div>
    </div>
    <address class="contact" style="font-style:normal">
      27 Calle Ámbar, Los Prados,<br>Santo Domingo<br>Dominican Republic
      <div class="contact__lines">
        <span class="contact__key">P:</span> +809 555 0101<br>
        <span class="contact__key">F:</span> +809 555 0102<br>
        <span class="contact__key">E:</span> info@zelvo.com.do
      </div>
      <div class="contact__web">www.zelvo.com.do</div>
    </address>
    <div class="exclaim-area" role="img" aria-label="Brand exclamation mark decoration"></div>
  </section>

  <section class="id-card" aria-label="Employee ID card">
    <svg class="id-card__band" viewBox="0 0 240 320" preserveAspectRatio="none" aria-hidden="true">
      <polygon points="60,0 240,0 240,320 110,320" fill="var(--red)"/>
    </svg>
    <div class="brand">
      <div class="wordmark">zelvo<span class="wordmark__dot"></span></div>
      <div class="wordmark__sub">PROMOTIONS GROUP</div>
    </div>
    <div class="id-card__holder">
      <div class="id-card__name">MATEO <strong>ROSAL</strong><span class="id-card__flag"></span></div>
      mateo.rosal@zelvo.com.do<br>809-555-0142
    </div>
    <div class="id-card__web">www.zelvo.com.do</div>
    <div class="id-card__badge">
      <div class="id-card__badge-id">ID</div>
      <div class="id-card__badge-card">CARD</div>
    </div>
  </section>

</body>
</html>
```